Whitcombe Business Card Design

The name of the business is Dario Whitcombe, CPA LLC
The service that we offer is Accounting, Tax & Consulting Services. I need it to have the following items:
Dario Whitcombe, Principal
Phone Number
Email Address
Physical Address

I have attached the company logo, one in black and one in white. Please provide a design in black background and the other in white background. Please include "Accounting, Tax & Consulting Services". I want the business card to be clean and very professional.

```html
<!DOCTYPE html>
<html lang="en">
<head>
<meta charset="utf-8">
<title>Dario Whitcombe, CPA LLC — Business Card</title>
<link rel="stylesheet" href="https://fonts.googleapis.com/css2?family=Montserrat:wght@500;600;700&family=Roboto:wght@400&display=swap">
<style>
  :root {
    --bg: #2a2a2a;
    --card-light: #f1f1f1;
    --card-shade: #e2e2e2;
    --brand-red: #8c1a1f;
    --ink-dark: #333333;
    --ink-grey: #7b7b7b;
    --band-grey: #8a8a8a;
  }
  * { margin: 0; padding: 0; box-sizing: border-box; }
  html, body {
    width: 1200px; height: 1138px; overflow: hidden;
    background: var(--bg);
  }
  .card {
    position: absolute;
    left: 273px;
    width: 621px;
    height: 376px;
    border-radius: 14px;
    overflow: hidden;
    background: linear-gradient(160deg, var(--card-light) 0%, var(--card-shade) 100%);
    text-align: center;
    color: var(--ink-dark);
  }
  .card--front { top: 184px; }
  .card--back { top: 606px; }
  .card__band {
    position: absolute; left: 0; right: 0; bottom: 0; height: 9px;
    display: flex;
  }
  .card__band span { flex: 1; }
  .card__band .band-red { background: var(--brand-red); }
  .card__band .band-grey { background: var(--band-grey); }

  .brand-mark {
    position: absolute; left: 50%; top: 96px;
    width: 64px; height: 64px; margin-left: -32px;
    background: var(--ink-dark);
  }
  .brand-name {
    position: absolute; left: 0; right: 0; top: 198px;
    font-family: "Montserrat", sans-serif; font-weight: 600;
    font-size: 25px; letter-spacing: 0.3px;
    color: var(--ink-dark);
  }
  .brand-tagline {
    position: absolute; left: 0; right: 0; top: 232px;
    font-family: "Montserrat", sans-serif; font-weight: 600;
    font-size: 17px; letter-spacing: 2.2px;
    color: var(--ink-grey);
  }
  .services {
    position: absolute; left: 0; right: 0; top: 326px;
    font-family: "Roboto", sans-serif; font-size: 15.5px;
    color: var(--ink-dark);
  }

  .person-name {
    position: absolute; left: 0; right: 0; top: 236px;
    font-family: "Montserrat", sans-serif; font-weight: 700;
    font-size: 21px; color: var(--brand-red); letter-spacing: 0.3px;
  }
  .person-role {
    position: absolute; left: 0; right: 0; top: 262px;
    font-family: "Roboto", sans-serif; font-size: 15.5px;
    color: var(--ink-grey);
  }
  .contact {
    position: absolute; left: 0; right: 0;
    font-family: "Roboto", sans-serif; font-size: 15px;
    color: var(--ink-dark); white-space: nowrap;
  }
  .contact--line1 { top: 297px; }
  .contact--line2 { top: 321px; }
  .contact .label { color: var(--brand-red); }
  .contact .sep { color: var(--brand-red); margin: 0 6px; }
</style>
</head>
<body>
  <section class="card card--front">
    <div class="brand-mark" aria-hidden="true"></div>
    <div class="brand-name">DARIO WHITCOMBE, CPA, LLC</div>
    <div class="brand-tagline">CERTIFIED PUBLIC ACCOUNTANT</div>
    <div class="services">Accounting, Tax &amp; Consulting Services</div>
    <div class="card__band"><span class="band-red"></span><span class="band-grey"></span></div>
  </section>

  <section class="card card--back">
    <div class="person-name">DARIO WHITCOMBE</div>
    <div class="person-role">Principal</div>
    <div class="contact contact--line1">
      <span class="label">P:</span> 828-555-0147<span class="sep">|</span><span class="label">E:</span> dw@dariowhitcombecpa.com<span class="sep">|</span><span class="label">W:</span> dariowhitcombecpa.com
    </div>
    <div class="contact contact--line2">
      <span class="label">A:</span> 5678, Sample Avenue, Any Town Name, US 654321
    </div>
    <div class="card__band"><span class="band-red"></span><span class="band-grey"></span></div>
  </section>
</body>
</html>
```